Business card for my new company (Accounting firm)

I need a business card for my new business Brightwell Advisory and Ledger SA. Our services are accounting, tax, audit and financial management. Our customers are small companies, start-ups and new companies. The final design has to show financial security, trust and growth. Please find our logo attached to the business card. Text for the business card: Brightwell Advisory and Ledger SA Tomas Varenholt Director and Founder Certified Accountant Tel. 022 418 57 34 tv@clairevalconseil.ch www.clairevalconseil.ch Rue des Vergières 27 1201 Geneva
Target Market(s)
Our customers are small companies, start-ups and new companies.
Industry/Entity Type
Finance And Accounting
Contact Information for Business Card
Claireval Conseil et Comptes SA
Tomas Varenholt
Directeur et Fondateur
Expert-comptable diplômé
Tél. 022 418 57 34
tv@clairevalconseil.ch
www.clairevalconseil.ch
Rue des Vergières 27
1201 Genève

```html
<!DOCTYPE html>
<html lang="fr">
<head>
<meta charset="utf-8">
<title>Claireval Conseil et Comptes SA – Carte de visite</title>
<link href="https://fonts.googleapis.com/css2?family=Roboto:wght@400;500;700&display=swap" rel="stylesheet">
<style>
  :root {
    --backdrop: #e6e7e9;
    --paper: #f7f7f7;
    --brand-light: #2ba3d8;
    --brand: #1f82bf;
    --brand-deep: #1a5f96;
    --ink: #3a3a3a;
    --ink-soft: #555;
    --charcoal: #3b3b3b;
  }
  * { box-sizing: border-box; margin: 0; padding: 0; }
  html, body { width: 1200px; height: 726px; overflow: hidden; }
  body {
    background: var(--backdrop);
    font-family: "Roboto", Arial, sans-serif;
    position: relative;
  }
  .card {
    position: absolute;
    top: 214px;
    width: 520px;
    height: 297px;
    border-radius: 4px;
    overflow: hidden;
    box-shadow: 0 6px 18px rgba(0,0,0,0.12);
  }
  /* Back side */
  .card-back {
    left: 50px;
    background: linear-gradient(160deg, var(--brand-light) 0%, var(--brand) 55%, var(--brand-deep) 100%);
    color: #fff;
    text-align: center;
  }
  .card-back .wordmark {
    position: absolute;
    top: 92px; left: 0; right: 0;
    font-weight: 500;
    color: #fff;
    line-height: 1;
  }
  .card-back .wordmark-name {
    display: block;
    font-size: 46px;
    letter-spacing: 6px;
  }
  .card-back .wordmark-sub {
    display: block;
    margin-top: 8px;
    font-size: 15px;
    letter-spacing: 4.5px;
  }
  .card-back .web {
    position: absolute;
    bottom: 52px; left: 0; right: 0;
    font-size: 14px;
    font-weight: 500;
    letter-spacing: 0.3px;
  }
  /* Front side */
  .card-front {
    left: 630px;
    background: var(--paper);
  }
  .brand {
    position: absolute;
    top: 44px; right: 34px;
    display: flex;
    align-items: center;
    gap: 10px;
  }
  .brand-square {
    width: 30px; height: 30px;
    background: var(--brand);
  }
  .brand-name {
    font-weight: 500;
    color: var(--brand-deep);
    line-height: 1;
  }
  .brand-name .line1 { display: block; font-size: 28px; letter-spacing: 3px; }
  .brand-name .line2 { display: block; font-size: 10px; letter-spacing: 2.6px; margin-top: 4px; }
  .person {
    position: absolute;
    top: 124px; left: 38px;
  }
  .person-name {
    font-size: 22px;
    font-weight: 700;
    color: var(--brand-deep);
  }
  .person-role {
    font-size: 12px;
    color: var(--ink-soft);
    line-height: 1.3;
    margin-top: 4px;
  }
  .contact {
    position: absolute;
    left: 38px; top: 214px;
    list-style: none;
    font-size: 13px;
    color: var(--ink);
  }
  .contact li {
    display: flex;
    align-items: center;
    gap: 10px;
    height: 19px;
  }
  .contact svg { width: 13px; height: 13px; fill: var(--brand-deep); flex: none; }
  .address-band {
    position: absolute;
    left: 0; bottom: 0;
    width: 520px; height: 70px;
  }
  .address {
    position: absolute;
    left: 278px; right: 12px;
    bottom: 14px;
    height: 50px;
    display: flex;
    align-items: center;
    justify-content: center;
    font-size: 12px;
    color: #fff;
    white-space: nowrap;
  }
</style>
</head>
<body>

  <section class="card card-back" aria-label="Verso de la carte">
    <div class="wordmark">
      <span class="wordmark-name">CLAIREVAL</span>
      <span class="wordmark-sub">CONSEIL ET COMPTES</span>
    </div>
    <p class="web">www.clairevalconseil.ch</p>
  </section>

  <section class="card card-front" aria-label="Recto de la carte">
    <div class="brand">
      <span class="brand-square"></span>
      <p class="brand-name">
        <span class="line1">CLAIREVAL</span>
        <span class="line2">CONSEIL ET COMPTES</span>
      </p>
    </div>

    <div class="person">
      <h1 class="person-name">Tomas Varenholt</h1>
      <p class="person-role">Directeur et Fondateur<br>Expert-comptable diplômé</p>
    </div>

    <ul class="contact">
      <li>
        <svg viewBox="0 0 16 16" aria-hidden="true"><path d="M3 1h3l1.5 4-2 1.3a9 9 0 0 0 4.2 4.2L11 8.5l4 1.5v3c0 1-1 2-2 2C6.4 15 1 9.6 1 3c0-1 1-2 2-2z"/></svg>
        022 418 57 34
      </li>
      <li>
        <svg viewBox="0 0 16 16" aria-hidden="true"><path d="M1 3h14v10H1z M2 4l6 5 6-5" fill="none" stroke="#1a5f96" stroke-width="1.6"/></svg>
        tv@clairevalconseil.ch
      </li>
      <li>
        <svg viewBox="0 0 16 16" aria-hidden="true"><circle cx="8" cy="8" r="6.5" fill="none" stroke="#1a5f96" stroke-width="1.5"/><path d="M1.5 8h13M8 1.5c-3 3.5-3 9.5 0 13M8 1.5c3 3.5 3 9.5 0 13" fill="none" stroke="#1a5f96" stroke-width="1.2"/></svg>
        www.clairevalconseil.ch
      </li>
    </ul>

    <svg class="address-band" viewBox="0 0 520 70" aria-hidden="true">
      <defs>
        <linearGradient id="bandFill" x1="0" x2="1">
          <stop offset="0" stop-color="#1a5f96"/>
          <stop offset="1" stop-color="#2ba3d8"/>
        </linearGradient>
      </defs>
      <path d="M226 58 C232 48 238 46 248 46 H520 V70 H226 Z" fill="#3b3b3b"/>
      <path d="M266 56 V20 C266 10 272 6 282 6 H520 V56 Z" fill="url(#bandFill)"/>
    </svg>
    <p class="address">Rue des Vergières 27 1201 Genève</p>
  </section>

</body>
</html>
```